I need a business card designed using the logo provided either vertical or horizontal......Harbourline Property Group is an Australian based real estate company that caters for the upper end of the market so the design of the business card "must reflect" the companies image!!
Colour combinations are optional but "must be realistic" and must be able to be accurately useable CMYK colours.
Please consider that any colours used "must be able to be used" and be suitable in following designs for "pull out banner signs" and "real estate signs".
The colours and the font in the attached designs are for example and other combinations are encouraged.
Target Market(s)
The High End of the Australian real estate market
Industry/Entity Type
Business
Contact Information for Business Card
Logo - Business Name - Director + Licensed Real Estate Agent - Mobile Number (Cell Phone) - Business Number - Fax - Email Address - Web address
Requirements
Must have
- Designs and colours (CMYK) that can easily be interpreted by an Australian printer.
Nice to have
- Some alternative ideas on colour and font..........the ones provided are ok and have been provided as an example but I am looking for alternative ideas
Should not have
- Loud, overly bright colours. Designs that do not reflect the professional standards of the business.
- Designs that look good on a computer monitor but can not be re-created on a printing press.............this is most important when it comes to shading etc.

```html
<!DOCTYPE html>
<html lang="en">
<head>
<meta charset="utf-8">
<title>Harbourline Property Group – Business Card</title>
<link rel="stylesheet" href="https://fonts.googleapis.com/css2?family=Source+Sans+3:wght@400;600&display=swap">
<style>
  :root {
    --backdrop: #141414;
    --cream: #f5f1e4;
    --cream-edge: #ece6d3;
    --gold: #b8852f;
    --gold-text: #c0913a;
    --ink: #2b2723;
    --ink-soft: #3a352f;
    --white: #ffffff;
  }
  * { margin: 0; padding: 0; box-sizing: border-box; }
  html, body { width: 1200px; height: 900px; overflow: hidden; }
  body {
    background: var(--backdrop);
    font-family: "Source Sans 3", sans-serif;
    position: relative;
  }
  .card {
    position: absolute;
    border-radius: 12px;
    overflow: hidden;
  }
  .card--front {
    left: 154px; top: 310px; width: 431px; height: 250px;
    background: linear-gradient(135deg, var(--cream) 0%, var(--cream-edge) 100%);
  }
  .card--back {
    left: 630px; top: 308px; width: 434px; height: 252px;
    background: var(--gold);
  }
  .brand-mark {
    position: absolute;
    display: block;
  }
  .card--front .brand-mark {
    left: 88px; top: 62px; width: 64px; height: 64px;
    background: var(--gold);
  }
  .card--back .brand-mark {
    left: 74px; top: 86px; width: 74px; height: 74px;
    background: var(--white);
  }
  .brand {
    position: absolute;
    font-weight: 600;
    text-transform: uppercase;
    text-align: center;
    line-height: 1.15;
  }
  .card--front .brand {
    left: 20px; top: 152px; width: 200px;
    color: var(--ink);
    font-size: 19px;
    letter-spacing: 1.5px;
  }
  .card--back .brand {
    left: 158px; top: 104px; width: 230px;
    color: var(--white);
    font-size: 27px;
    letter-spacing: 2px;
  }
  .brand span { display: block; font-size: 0.62em; letter-spacing: 0.35em; margin-top: 4px; }
  .card--back .brand span { letter-spacing: 0.3em; }
  .contact {
    position: absolute;
    left: 229px; top: 48px;
    color: var(--ink-soft);
    font-size: 13px;
    line-height: 1.25;
  }
  .contact__name {
    color: var(--gold-text);
    font-size: 18px;
    font-weight: 600;
    line-height: 1.1;
  }
  .contact__role { margin-top: 1px; }
  .contact__address { margin-top: 14px; }
  .contact__lines { list-style: none; margin-top: 13px; }
  .contact__lines li { display: flex; align-items: center; height: 16.3px; }
  .contact__lines svg { width: 9px; height: 9px; margin-right: 8px; fill: var(--gold); flex: none; }
</style>
</head>
<body>
  <section class="card card--front">
    <span class="brand-mark" aria-hidden="true"></span>
    <div class="brand">Harbourline<span>Property Group</span></div>
    <div class="contact">
      <p class="contact__name">Daniel Whitford</p>
      <p class="contact__role">Managing Director</p>
      <p class="contact__address">18 Wharf Street<br>Sydney NSW, 2000</p>
      <ul class="contact__lines">
        <li><svg viewBox="0 0 10 10" aria-hidden="true"><rect x="2.5" y="0" width="5" height="10" rx="1"/><rect x="3.5" y="1.5" width="3" height="6" fill="#f5f1e4"/></svg>0412-555-018</li>
        <li><svg viewBox="0 0 10 10" aria-hidden="true"><path d="M0 4 Q5 0 10 4 L8 5 L7 3.5 L3 3.5 L2 5Z"/><rect x="2" y="5" width="6" height="4"/></svg>02-5550-1842</li>
        <li><svg viewBox="0 0 10 10" aria-hidden="true"><rect x="2" y="0" width="6" height="4"/><rect x="0" y="4" width="10" height="6" rx="1"/></svg>02-5550-1843</li>
        <li><svg viewBox="0 0 10 10" aria-hidden="true"><rect x="0" y="2" width="10" height="7"/><path d="M0 2 L5 6 L10 2" stroke="#f5f1e4" stroke-width="1" fill="none"/></svg>info@harbourline.au</li>
        <li><svg viewBox="0 0 10 10" aria-hidden="true"><path d="M6 1 L9 4 L4 9 L1 6Z" fill="none" stroke="#b8852f" stroke-width="1.6"/></svg>www.harbourline.au</li>
      </ul>
    </div>
  </section>

  <section class="card card--back">
    <span class="brand-mark" aria-hidden="true"></span>
    <div class="brand">Harbourline<span>Property Group</span></div>
  </section>
</body>
</html>
```